New Food Sleeve Design for British Traditional Food Manufacture - est 1976

We are a food manufacturer of a British traditional Steamed 'Rag Pudding' this is a Lancashire traditional dish. It consists of finest cuts of beef, hand wrapped in a suet pastry. Then traditionally wrapped in a rag (muslin cloth) today we use a modern plastic version to wrap the pudding then it is steamed, to create a beautiful tasting beef pudding (which is essentially a pie or parcel).
We are looking for a design on a newly developed packaging, which is basically a sleeve with two stays at either end so the product can not slip out of the packaging.
We would like to see designs that have :
1. a picture of the cooked product on the top of the sleeve - so customers can see what they will get once cooked.
2. The bottom of the package is for the ingredients, barcode best before date - We have this in hand so please do not design anything on the bottom of the package.
3.The front with the push tap and the opposite rear can be for cooking instructions or further info - we have no preference ein this area.
4. Wording/art required:
- Picture of the cooked product (I have a photo attached that can be used for now - but we intend to upgrade this photo at a later)
- Picture of the little man - however this man can be upgraded as it is 40 years old
- Wording 'Est 1976'
- if possible a British flag & wording 'Made in Britain'
=Wording 'Pemberton's Beef Pudding'
- Cooking instructions - maybe use of symbols - Oven bake, Steam, Boil in the bag, Microwave. But these could potentially go on the smaller front or rear location
- We would like a black, dark grey etc colour as the background - we feel this is currently a luxurious/quality look' at the moment.
- But we are open to other colours if you want to experiment

Info attached to help you...
- We have attached the pdf of the dimensions of the packaging
- Photo of beef pudding - happy for you to remove the chips and peas if that helps
- Link to current website - www.steamparcelworks.co.uk
- The little man (as mentioned happy for an upgrade) we don't need the writing along with the little man
- a few photos of how the packaging works and looks (photos of stages 1 to 6)
- a few design attached of what we like, but we are not stuck to this happy to see different ideas

Update 19th January 2023
We have lots of great designs, each with parts we like. I'd like to provide some overall feedback of the items we like from the designs submitted to date:
-The little man logo. We really like the British flag represented on the apron. We think if Pembertons dale larder can be removed from this logo and keep the words 'quality with convenience', 'made in Britain ' & EST 1976. I think that would be great.
-we think the pudding on its own rather than with chips and peas looks better and gives a clear indication of what the customer is buying.
-we don't need sell by/best before/batch number on the front as this will be on the rear and on the internal packaging
-do like/need the colour chart for salt/sugar/fat etc - but currently have no preference to if it's on the top or front.
-do like the symbols for cooking, but not sure we like one we have seen yet.
-lile the idea of golden/golden orange colour text in places
-really like the slight band of colour as this could be simple changed to an alternative colour for other products with have.
Hope this helps you all

Target Market(s)

Basically anyone who has an evening meal who likes to eat meat

Industry/Entity Type

Food maufacturing

Colors

Designer to choose colors to be used in the design.

Requirements
Must have
• A picture of the product when cooked
Nice to have
• Little man, established 1976, made in Britain

```html
<!DOCTYPE html>
<html lang="en">
<head>
<meta charset="utf-8">
<title>Pemberton's Beef Pudding – Sleeve</title>
<link href="https://fonts.googleapis.com/css2?family=Righteous&family=Roboto+Condensed:wght@400;700&family=Montserrat:wght@400;600;800&display=swap" rel="stylesheet">
<style>
  :root{
    --ground:#d4d8df;
    --black:#000;
    --white:#fff;
    --red:#e01b1b;
    --gold:#f1c65a;
    --gold-deep:#c9962c;
    --royal:#1f35a8;
    --royal-deep:#142073;
    --cut:#7cc3e6;
    --ink:#111;
  }
  *{box-sizing:border-box;margin:0;padding:0}
  html,body{width:1200px;height:2267px;overflow:hidden;background:var(--ground)}
  .canvas{position:relative;width:1200px;height:2267px;overflow:hidden}
  .sleeve{position:absolute;left:50px;top:360px;width:1100px;height:1548px}

  /* top flap – cooking instructions, printed upside down */
  .flap-top{position:absolute;left:0;top:0;width:1100px;height:220px;background:var(--black);color:var(--white);transform:rotate(180deg);font-family:"Roboto Condensed",sans-serif}
  .flap-top h3{position:absolute;left:30px;top:22px;font-family:"Montserrat",sans-serif;font-weight:800;font-size:17px;letter-spacing:.5px}
  .methods{position:absolute;left:30px;top:62px;display:flex;align-items:center}
  .method{display:flex;align-items:center;gap:20px;width:345px;padding-right:20px}
  .method + .method{border-left:3px solid var(--white);padding-left:40px}
  .method svg{flex:none}
  .method p{font-size:17px;line-height:23px}

  /* top panel */
  .panel-top{position:absolute;left:0;top:220px;width:1100px;height:497px;background:var(--black)}
  .red-rule{position:absolute;top:0;width:6px;height:497px;background:var(--red)}
  .brand-block{position:absolute;left:0;top:0;width:490px;height:497px;text-align:center}
  .maker{position:absolute;left:0;width:490px;top:38px;font-family:"Righteous",sans-serif;color:var(--red);font-size:30px;line-height:30px}
  .maker small{display:block;font-size:19px;line-height:22px}
  .tagline{position:absolute;left:70px;top:120px;width:360px;height:46px;border-radius:23px;background:var(--gold);color:var(--royal);font-family:"Righteous",sans-serif;font-size:23px;line-height:46px;transform:rotate(2deg)}
  .ribbon{position:absolute;left:0;top:167px}
  .product-name{position:absolute;left:0;top:200px;width:560px;text-align:center;font-family:"Righteous",sans-serif;color:var(--gold)}
  .product-name .maker-line{display:block;font-size:30px;line-height:36px;padding-left:40px}
  .product-name .dish{display:block;font-size:78px;line-height:82px;letter-spacing:1px}
  .est{position:absolute;left:175px;top:392px;width:145px;height:34px;border-radius:17px;background:var(--gold);color:var(--royal);font-family:"Righteous",sans-serif;font-size:21px;line-height:34px}
  .web{position:absolute;left:0;width:490px;top:455px;color:var(--white);font-family:"Montserrat",sans-serif;font-size:15px}
  .product-photo{position:absolute;left:490px;top:0;width:610px;height:497px;background:
    radial-gradient(ellipse 46% 34% at 52% 52%,#d79a42 0%,#c98a3a 45%,rgba(201,138,58,0) 75%),
    radial-gradient(ellipse 62% 46% at 55% 58%,#f2f2f2 0%,#dcdcdc 70%,rgba(220,220,220,0) 88%),
    linear-gradient(160deg,#3a3a3a,#1e1e1e)}
  .weight{position:absolute;left:508px;top:448px;color:var(--white);font-family:"Montserrat",sans-serif;font-weight:600;font-size:28px}
  .seal{position:absolute;left:955px;top:335px;width:146px;height:146px;border-radius:50%;background:var(--gold-deep);border:6px solid var(--gold)}

  /* front panel */
  .panel-front{position:absolute;left:0;top:717px;width:1100px;height:227px;background:var(--black);color:var(--white);font-family:"Roboto Condensed",sans-serif;font-size:25px;line-height:31px;text-align:center;padding:42px 210px 0}

  /* white back area */
  .panel-back{position:absolute;left:0;top:944px;width:1100px;height:604px;font-family:"Roboto Condensed",sans-serif;color:var(--ink)}
  .dieline{position:absolute;left:0;top:0}
  .tab-note{position:absolute;left:250px;top:28px;width:600px;text-align:center;font-size:18px;line-height:24px}
  .tab-note b{font-family:"Montserrat",sans-serif;font-weight:800}
  .rotated{position:absolute;transform:rotate(90deg);transform-origin:center}
  .back-copy{left:305px;top:175px;width:274px;height:280px;font-size:17.5px;line-height:25px}
  .back-copy p{margin-bottom:8px}
  .back-copy p:first-child{text-indent:22px}
  .nutrition{left:700px;top:1034px;width:272px;height:453px;border:1px solid #333;padding:8px 10px;font-size:13.5px;line-height:17px;background:var(--white)}
  .nutrition{top:90px}
  .nutrition h4{font-family:"Montserrat",sans-serif;font-weight:800;font-size:30px;line-height:34px;border-bottom:8px solid #000;padding-bottom:2px}
  .nutrition .row{display:flex;justify-content:space-between;border-bottom:1px solid #555}
  .nutrition .thick{border-bottom:5px solid #000}
  .nutrition .ind{padding-left:14px}
  .nutrition .note{font-size:12.5px;line-height:15px;margin-top:6px}
</style>
</head>
<body>
<div class="canvas">
  <div class="sleeve">

    <section class="flap-top">
      <h3>LOREM IPSUM DOLOR SIT AMET.</h3>
      <div class="methods">
        <div class="method">
          <svg width="92" height="82" viewBox="0 0 92 82" aria-label="Steam icon" role="img">
            <rect x="10" y="20" width="72" height="24" rx="6" fill="#fff"/>
            <rect x="0" y="26" width="92" height="8" rx="4" fill="#fff"/>
            <rect x="34" y="12" width="24" height="10" rx="3" fill="#fff"/>
            <path d="M34 52 q6 6 0 12 q-6 6 0 12 M46 52 q6 6 0 12 q-6 6 0 12 M58 52 q6 6 0 12 q-6 6 0 12" stroke="#fff" stroke-width="3" fill="none"/>
          </svg>
          <p>Lorem ipsum dolor sit<br>amet, consectetuer<br>adipiscing elit.</p>
        </div>
        <div class="method">
          <svg width="96" height="66" viewBox="0 0 96 66" aria-label="Microwave icon" role="img">
            <rect x="2" y="2" width="92" height="62" rx="4" fill="#fff"/>
            <rect x="8" y="8" width="14" height="50" fill="#000"/>
            <rect x="11" y="14" width="8" height="6" fill="#fff"/>
            <rect x="11" y="26" width="8" height="4" fill="#fff"/>
            <rect x="28" y="8" width="60" height="50" fill="#000"/>
            <rect x="33" y="13" width="50" height="40" fill="#fff"/>
            <path d="M42 30 l5 -4 l5 4 l5 -4 l5 4 l5 -4 l5 4 M42 40 l5 -4 l5 4 l5 -4 l5 4 l5 -4 l5 4" stroke="#000" stroke-width="3" fill="none"/>
          </svg>
          <p>Consectetuer<br>adipiscing elit, sed<br>diam nonummy nibh</p>
        </div>
        <div class="method">
          <svg width="72" height="86" viewBox="0 0 72 86" aria-label="Oven icon" role="img">
            <rect x="2" y="2" width="68" height="76" rx="3" fill="#fff"/>
            <rect x="10" y="10" width="52" height="46" fill="#000"/>
            <path d="M24 18 q6 6 0 12 q-6 6 0 12 M36 18 q6 6 0 12 q-6 6 0 12 M48 18 q6 6 0 12 q-6 6 0 12" stroke="#fff" stroke-width="3" fill="none"/>
            <circle cx="14" cy="67" r="4" fill="#000"/><circle cx="26" cy="67" r="4" fill="#000"/><circle cx="38" cy="67" r="4" fill="#000"/><circle cx="50" cy="67" r="4" fill="#000"/>
            <rect x="6" y="78" width="8" height="6" fill="#fff"/><rect x="58" y="78" width="8" height="6" fill="#fff"/>
          </svg>
          <p>Ut wisi enim ad minim<br>veniam, quis nostrud<br>exerci tation corth</p>
        </div>
      </div>
    </section>

    <section class="panel-top">
      <div class="product-photo" role="img" aria-label="Photo of the cooked beef pudding with gravy on a white plate"></div>
      <div class="red-rule" style="left:16px"></div>
      <div class="red-rule" style="left:470px"></div>
      <div class="brand-block">
        <div class="maker">Pembertons<small>dale larder</small></div>
        <div class="tagline">Quality With Convenience</div>
      </div>
      <svg class="ribbon" width="580" height="200" viewBox="0 0 580 200">
        <path d="M0 16 C160 0 360 -4 520 20 C560 26 566 60 560 90 L580 190 C420 168 200 168 0 192 Z" fill="var(--royal)"/>
        <path d="M0 16 C160 0 360 -4 520 20" stroke="var(--gold)" stroke-width="3" fill="none"/>
        <path d="M0 192 C200 168 420 168 580 190" stroke="var(--gold)" stroke-width="3" fill="none"/>
        <path d="M520 20 C560 26 566 60 560 90 L540 60 Z" fill="var(--royal-deep)"/>
      </svg>
      <div class="product-name">
        <span class="maker-line">Pemberton's</span>
        <span class="dish">Beef Pudding</span>
      </div>
      <div class="brand-block" style="pointer-events:none">
        <div class="est">• Est 1976 •</div>
        <div class="web">www.steamparcelworks.co.uk</div>
      </div>
      <div class="weight">330g ℮</div>
      <div class="seal" role="img" aria-label="Quality seal"></div>
    </section>

    <section class="panel-front">
      Lorem ipsum dolor sit amet, consectetuer adipiscing elit, sed diam nonummy nibh euismod tincidunt ut laoreet dolore magna aliquam erat volutpat. Ut wisi enim ad minim veniam, quis nostrud exerci tation ullamcorper suscipit lobortis nisl ut aliquip ex ea commodo consequat.
    </section>

    <section class="panel-back">
      <svg class="dieline" width="1100" height="604" viewBox="0 0 1100 604" fill="none" stroke="var(--cut)" stroke-width="1.5">
        <path d="M157 0 L203 141 L0 141 M942 0 L897 141 L1100 141"/>
        <path d="M0 0 L0 498 L29 604 L1071 604 L1100 498 L1100 0"/>
        <path d="M0 498 L1100 498" stroke-dasharray="12 8"/>
      </svg>
      <p class="tab-note"><b>LOREM IPSUM DOLOR SIT AMET</b>, consectetuer adipiscing elit, sed diam nonummy nibh euismod tincidunt ut laoreet dolore magna aliquam erat volutpat. Ut wisi enim ad minim veniam, quis nostrud exerci tation ullamcorper suscipit lobortis nisl ut aliquip ex ea commodo consequat.</p>

      <div class="rotated back-copy" style="top:185px">
        <p>Lorem ipsum dolor sit amet, consectetuer adipiscing elit, sed diam nonummy nibh euismod tincidunt ut laoreet dolore magna aliquam erat volutpat. Ut wisi enim ad minim veniam, quis nostrud exerci tation ullamcorper suscipit lobortis nisl ut aliquip ex ea commodo consequat.</p>
        <p>Duis autem vel eum iriure dolor in umy nibh euismod tincidu nibh out ins the tincidunt ut laoreet dolore magna</p>
      </div>

      <div class="rotated nutrition" style="left:700px">
        <h4>Nutrition Facts</h4>
        <div>Serving Size oz.</div>
        <div class="thick">Serving Per Container</div>
        <div style="font-size:12px">Amount Per Serving:</div>
        <div class="row"><span>Calories</span><span>Calories From Fat</span></div>
        <div class="row" style="justify-content:flex-end"><b>% Daily value*</b></div>
        <div class="row"><b>Total Fat</b><span>%</span></div>
        <div class="row ind"><span>Saturated Fat</span><span>%</span></div>
        <div class="row ind"><span>Trans Fat</span></div>
        <div class="row"><b>Cholesterol</b><span>%</span></div>
        <div class="row"><b>Sodium</b><span>%</span></div>
        <div class="row"><b>Total Carbohydrate</b><span>%</span></div>
        <div class="row ind"><span>Dietary Fiber</span><span>%</span></div>
        <div class="row ind"><span>Sugars</span></div>
        <div class="row thick"><b>Protein</b></div>
        <p class="note">*Percent Daily values are based on a 2000 calorie diet. Your daily values may be higher or lower depending on you calorie needs.</p>
      </div>
    </section>

  </div>
</div>
</body>
</html>
```